Dentistry

Dentist's personal business card. No logo needed. The card shoul deliver the massage of reliability, professionalism, experience.
Please ad the full brief of the project: down the line it says: the winning look should be precise and pristine NO pictures of Teeth, smiles, instruments etc.

The details to be desplaid are:
Dr. Rob Tavolen
Doctor of Dental Surgery
PHD
Web. Www.drtavolen.com
Email. Rob@drtavolen.com
Tel 07742318590
Surgery address. 27Bferndale road London SW4 8QT UK
62 Wexley Row London SW3 2HN. Uk

Reason: Decided to make the payment unrefundable in order to get more designers involved.

Requirements
Should not have
• Logo, teeth, smile any sort of instruments.

```html
<!DOCTYPE html>
<html lang="en">
<head>
<meta charset="utf-8">
<title>Dr. Rob Tavolen – Business Card</title>
<link rel="stylesheet" href="https://fonts.googleapis.com/css2?family=Sacramento&family=Arimo:wght@600&family=Alegreya+Sans:wght@700&display=swap">
<style>
  :root {
    --page-bg: #e9e8e6;
    --front-light: #ffffff;
    --front-edge: #dcdcdc;
    --ink: #1a1a1a;
    --back-bg: #000000;
    --back-ink: #ffffff;
    --card-shadow: rgba(0, 0, 0, 0.35);
  }
  html, body {
    margin: 0;
    padding: 0;
    width: 1200px;
    height: 1200px;
    overflow: hidden;
    background: var(--page-bg);
  }
  .canvas {
    position: relative;
    width: 1200px;
    height: 1200px;
  }
  .card {
    position: absolute;
    left: 150px;
    width: 884px;
    height: 506px;
    overflow: hidden;
    box-shadow: 4px 6px 10px var(--card-shadow);
  }
  .card-front {
    top: 46px;
    background: radial-gradient(ellipse at 55% 60%, var(--front-light) 0%, #f3f3f3 45%, var(--front-edge) 100%);
  }
  .card-back {
    top: 624px;
    background: var(--back-bg);
  }
  .doctor-name {
    position: absolute;
    left: 130px;
    top: 168px;
    margin: 0;
    font-family: "Sacramento", cursive;
    font-weight: 400;
    font-size: 88px;
    line-height: 1;
    color: var(--ink);
    white-space: nowrap;
  }
  .doctor-title {
    position: absolute;
    left: 138px;
    top: 302px;
    margin: 0;
    font-family: "Arimo", Arial, sans-serif;
    font-weight: 600;
    font-size: 28px;
    line-height: 1;
    color: var(--ink);
    white-space: nowrap;
  }
  .contact-list {
    position: absolute;
    inset: 0;
    margin: 0;
    padding: 0;
    list-style: none;
    font-family: "Alegreya Sans", "Trebuchet MS", sans-serif;
    font-weight: 700;
    font-size: 33px;
    color: var(--back-ink);
  }
  .contact-item {
    position: absolute;
    left: 0;
    right: 0;
    height: 40px;
    line-height: 40px;
    text-align: center;
    white-space: nowrap;
  }
  .contact-phone { top: 110px; letter-spacing: 3px; }
  .contact-email { top: 169px; letter-spacing: 2.5px; }
  .contact-web   { top: 236px; letter-spacing: 0.5px; }
  .contact-surgery { top: 289px; }
  .contact-second-surgery { top: 355px; }
</style>
</head>
<body>
  <main class="canvas">
    <section class="card card-front" aria-label="Business card front">
      <h1 class="doctor-name">Dr. Rob Tavolen</h1>
      <p class="doctor-title">Doctor of Dental Surgery, PHD</p>
    </section>
    <section class="card card-back" aria-label="Business card back">
      <ul class="contact-list">
        <li class="contact-item contact-phone">Tel: 07742318590</li>
        <li class="contact-item contact-email">Email: Rob@drtavolen.com</li>
        <li class="contact-item contact-web">Web: www.drtavolen.com</li>
        <li class="contact-item contact-surgery">Surgery address. 27Bferndale road London SW4 8QT UK</li>
        <li class="contact-item contact-second-surgery">62 Wexley Row London SW3 2HN. Uk</li>
      </ul>
    </section>
  </main>
</body>
</html>
```